Local price comparison site needs a new design

We need new, prettier and especially more efficient, design for local (Slovak Republic) price comparison site. The old one (www.tulvenko.sk) is kind of ugly, but more importantly, it doesn't work for consumer audience (performance indicators are kind of bad). We've started something already, but we're just a bunch of amateurs in this area.

Our first attempt is in the attached file. Colors are such because of the logo (which is dark blue and the only given thing at the moment). The design is a combination and inspired by two other similar sites here:
www.brombilo.sk
www.plutavek.cz

We tried, but we're not designers...

Industry/Entity Type

Consumer

Colors

Designer to choose colors to be used in the design.

Requirements
Must have
• Efficient design from performance perspective (we want people to click a lot, content will be attractive enough, we don't want the design to be in the way, but support this)
Vertical banners stripe on the (right) side (see both old and our attempt at new design)
We will need several pages designed (main, category page, product page, search page), but I am not sure how to indicate this in the parameters of the project details
Nice to have
• Please make it simple and easy to read for consumers
Visual design with big pictures

```html
<!DOCTYPE html>
<html lang="sk">
<head>
<meta charset="utf-8">
<title>tulvenko.sk – porovnanie cien</title>
<link href="https://fonts.googleapis.com/css2?family=Arimo:wght@400;700&display=swap" rel="stylesheet">
<style>
:root{
  --blue:#2a5aa8;--link:#2f5f9e;--text:#555;--line:#cfd3d8;--bar:#5d6671;
  --btn:#5a6069;--bg:#fff;--soft:#eef1f5;--red:#b3121b;
}
*{box-sizing:border-box;margin:0;padding:0}
html,body{width:917px;height:1200px;overflow:hidden;background:var(--bg);font-family:"Arimo",Arial,sans-serif;color:var(--text)}
.page{position:relative;width:917px;height:1200px}
.abs{position:absolute}
.header{left:0;top:0;width:917px;height:89px;background:linear-gradient(#dfe6ef,#f3f6f9)}
.logo{font-weight:700;color:var(--blue);font-size:21px;display:flex;align-items:center;gap:6px}
.logo i{width:14px;height:14px;border-radius:50%;background:var(--blue);display:inline-block}
.search{left:382px;top:35px;width:230px;height:24px;border:1px solid #c4c9cf;background:#fff;font-size:8px;color:#888;padding:7px 8px;white-space:nowrap;overflow:hidden}
.btn{top:35px;height:25px;background:var(--btn);color:#fff;font-size:10px;display:flex;align-items:center;justify-content:center;border-radius:2px}
.nav{left:72px;top:110px;width:145px;list-style:none}
.nav li{height:24.9px;border-bottom:1px solid var(--line);font-size:8px;display:flex;align-items:center;justify-content:space-between;padding:0 5px}
.nav li::after{content:"»";color:#999}
.hero{left:240px;top:110px;width:487px;height:203px;background:linear-gradient(120deg,#c8141c,#8f0c12)}
.hero .art{position:absolute;left:0;top:0;width:355px;height:203px;background:radial-gradient(circle at 40% 50%,#e23a3a,#a90f16)}
.hero h2{position:absolute;left:372px;top:42px;color:#fff;font-weight:400;font-size:22px}
.hero p{position:absolute;left:374px;top:74px;width:100px;color:#fff;font-size:9.5px;line-height:18px}
.hero .cta{position:absolute;left:373px;top:139px;width:100px;height:28px;background:#f3f3f3;border-radius:3px;color:var(--red);font-size:13px;display:flex;align-items:center;justify-content:center}
.bar{left:240px;top:326px;width:487px;height:28px;background:var(--bar);color:#fff;font-size:10.5px;padding:8px 14px}
.card{top:368px;width:153px;height:214px;border:1px solid #d8dbdf;background:linear-gradient(#f4f5f6,#fff);text-align:center}
.card .img{width:90px;height:100px;margin:14px auto 0;border-radius:4px}
.card h3{font-weight:400;color:var(--link);font-size:11px;margin-top:10px}
.card p{font-size:7px;line-height:12.5px;margin:6px 18px 0}
.card .sub{font-size:8px;color:var(--link);margin-top:10px;display:flex;justify-content:space-around}
.tag{left:243px;top:606px;font-size:9.5px;color:var(--link);white-space:nowrap}
.partner{top:632px;width:91px;height:46px;border:1px solid #d4d7db;display:flex;align-items:center;justify-content:center;gap:4px;font-size:9px;font-weight:700;color:#444;white-space:nowrap}
.partner i{width:9px;height:9px;border-radius:50%;display:inline-block;flex:none}
.col h4{font-weight:400;color:var(--link);font-size:11px;margin-bottom:8px;white-space:nowrap}
.col ul{list-style:none}
.col li{font-size:7px;height:15.7px;color:#555;white-space:nowrap}
.col li::before{content:"» ";color:#999}
.ad{background:linear-gradient(#2a2f3a,#171a20)}
.footer{left:0;top:932px;width:917px;height:185px;background:linear-gradient(#e9ecef,#fff 40%);border-top:2px solid #dde1e5}
.bottom{left:0;top:1117px;width:917px;height:83px;border-top:1px solid #dde1e5}
.social{top:1140px;width:20px;height:20px;border-radius:50%}
</style>
</head>
<body>
<div class="page">
  <header class="abs header"></header>
  <div class="abs logo" style="left:72px;top:52px"><i></i>tulvenko.sk</div>
  <div class="abs search">Cez 5.401.263 produktov, vyše 3.316 predajní ...</div>
  <div class="abs btn" style="left:619px;width:70px">Hľadaj</div>
  <div class="abs btn" style="left:697px;width:88px">Prihlásiť sa</div>

  <ul class="abs nav">
    <li>TV, DVD, foto</li><li>Mobily a komunikace</li><li>Počítače a hardware</li><li>Domácnost a kancelář</li><li>Auto-moto</li><li>Nářadí a zahrada</li><li>Sport a fitness</li><li>Audio a Mp3</li><li>Koníčky a outdoor</li><li>Děti a maminky</li><li>Erotika</li><li>Krása, zdraví a léky</li><li>Knihy, filmy, hudba</li><li>Software a Hry</li><li>Oblečení a móda</li><li>Nábytek a bytové doplňky</li><li>Hromadné slevy</li><li>Slevy dne</li><li>Soutěž</li>
  </ul>

  <section class="abs hero">
    <div class="art" role="img" aria-label="Vianočná ilustrácia s prianím veselých Vianoc a šťastného nového roka 2014"></div>
    <h2>Tulvenko</h2>
    <p>Vyzkoušejte srovnání cen zboží v těchto kategoriích:</p>
    <div class="cta">Click Here</div>
  </section>

  <div class="abs bar">Vyzkoušejte srovnání cen zboží v těchto kategoriích:</div>

  <div class="abs card" style="left:240px"><div class="img" role="img" aria-label="Fotografia tabletu" style="background:linear-gradient(#3a3a3a,#111)"></div><h3>Mobilní telefony</h3><p>Default model text, and a search for 'lorem ipsum' will uncover many web sites still in their infancy.</p><div class="sub"><span>Notebooky »</span><span>Chladničky »</span></div></div>
  <div class="abs card" style="left:407px"><div class="img" role="img" aria-label="Fotografia športovej tašky" style="background:linear-gradient(#e9c21a,#2a2a2a)"></div><h3>Mobilní telefony</h3><p>Default model text, and a search for 'lorem ipsum' will uncover many web sites still in their infancy.</p><div class="sub"><span>Notebooky »</span><span>Chladničky »</span></div></div>
  <div class="abs card" style="left:574px"><div class="img" role="img" aria-label="Fotografia zrkadlovky" style="background:linear-gradient(#555,#111)"></div><h3>Mobilní telefony</h3><p>Default model text, and a search for 'lorem ipsum' will uncover many web sites still in their infancy.</p><div class="sub"><span>Notebooky »</span><span>Chladničky »</span></div></div>

  <div class="abs tag">Muchas versiones han evolucionado a través de los años, algunas veces por accidente, otras veces a propósito...</div>
  <div class="abs partner" style="left:240px"><i style="background:#8a7a10"></i>giftlune</div>
  <div class="abs partner" style="left:339px"><i style="background:#2a6fb8"></i>Marlo Fenwick</div>
  <div class="abs partner" style="left:438px"><i style="background:#f08020"></i>brelix.de</div>
  <div class="abs partner" style="left:537px"><i style="background:#4aa8e0"></i>aquevo</div>
  <div class="abs partner" style="left:636px"><i style="background:#222"></i>snowlane</div>

  <div class="abs col" style="left:240px;top:699px"><h4>Poradna</h4><ul><li>Zimní pneumatiky</li><li>Tablety</li><li>Mobilní telefony</li><li>Pračky</li><li>Digitální fotoaparáty</li><li>LCD televize</li><li>všechny poradny</li></ul></div>
  <div class="abs col" style="left:371px;top:699px"><h4>Nejhledanější značky</h4><ul><li>Zimní pneumatiky</li><li>Tablety</li><li>Mobilní telefony</li><li>Pračky</li><li>Digitální fotoaparáty</li><li>LCD televize</li><li>všechny poradny</li></ul></div>
  <div class="abs col" style="left:508px;top:699px"><h4>Nejoblíbenější produkty</h4><ul><li>Zimní pneumatiky</li><li>Tablety</li><li>Mobilní telefony</li><li>Pračky</li><li>Digitální fotoaparáty</li><li>LCD televize</li><li>všechny poradny</li></ul></div>
  <div class="abs col" style="left:652px;top:699px"><h4>Poradna</h4><ul><li>Zimní pneumatiky</li><li>Tablety</li><li>Mobilní telefony</li><li>Pračky</li><li>Digitální fotoaparáty</li><li>LCD televize</li><li>všechny poradny</li></ul></div>

  <div class="abs" role="img" aria-label="Reklamný banner fakturačného softvéru Billquarn" style="left:245px;top:851px;width:476px;height:59px;background:linear-gradient(90deg,#cfe96a,#6aa82a);border:1px solid #4a7a20"></div>
  <div class="abs ad" role="img" aria-label="Vertikálny reklamný banner webhostingu Drebtonhost" style="left:744px;top:110px;width:79px;height:393px"></div>
  <div class="abs" role="img" aria-label="Vertikálny reklamný banner inzertnej služby Postvoro" style="left:744px;top:516px;width:79px;height:392px;background:linear-gradient(#1f3aa8,#2a4fd0 60%,#9aa8c8)"></div>

  <footer class="abs footer"></footer>
  <div class="abs col" style="left:240px;top:961px"><h4>O nás</h4><ul><li>Kto sme</li><li>Je nás vidieť</li><li>Na stiahnutie</li><li>Kontakt</li><li>Press</li><li>Obchodné podmienky</li><li>Podmienky registrácie</li><li>Mapa stránok</li></ul></div>
  <div class="abs col" style="left:416px;top:961px"><h4>Pre obchody</h4><ul><li>Zimní pneumatiky</li><li>Tablety</li><li>Mobilní telefony</li><li>Pračky</li><li>Digitální fotoaparáty</li><li>LCD televize</li><li>všechny poradny</li></ul></div>
  <div class="abs col" style="left:600px;top:961px"><h4>Pre návštevníkov</h4><ul><li>Zimní pneumatiky</li><li>Tablety</li><li>Mobilní telefony</li><li>Pračky</li><li>Digitální fotoaparáty</li><li>LCD televize</li><li>všechny poradny</li></ul></div>

  <div class="abs bottom"></div>
  <div class="abs logo" style="left:250px;top:1141px;font-size:15px"><i style="width:10px;height:10px"></i>tulvenko.sk</div>
  <div class="abs" style="left:360px;top:1135px;height:32px;border-left:1px solid #ccc"></div>
  <div class="abs" style="left:372px;top:1139px;font-size:9px;color:var(--link);white-space:nowrap">Tulvenko.sk, Najväčšia nákupná zóna na webe</div>
  <div class="abs" style="left:372px;top:1156px;font-size:7px;white-space:nowrap">Copyright © 2010-2014. Všetky práva vyhradené.</div>
  <div class="abs social" style="left:585px;background:#2d5fa8"></div>
  <div class="abs social" style="left:609px;background:#3fa3dc"></div>
  <div class="abs social" style="left:633px;background:#1f7fb0"></div>
  <div class="abs social" style="left:657px;background:#f0a020"></div>
  <div class="abs social" style="left:681px;background:#d8262f"></div>
  <div class="abs social" style="left:705px;background:#333"></div>
  <div class="abs" style="left:801px;top:1145px;font-size:9px;color:var(--link)">C8</div>
</div>
</body>
</html>
```